I need a SEO-friendly Wordpress website (making sure to style H1, H2, H3, etc correctly) for a Hawaii-based law firm called Meridian Crest Legal Group. Comparable websites include https://brvlaw.example/ and https://www.lomrit.example/ for design reference. The current copy on the TarnAdvocate.example website can be used.

```html
<!DOCTYPE html>
<html lang="en">
<head>
<meta charset="utf-8">
<title>Meridian Crest Legal Group – Divorce and Personal Injury Lawyers</title>
<link rel="stylesheet" href="https://fonts.googleapis.com/css2?family=Open+Sans:wght@400;600;700&display=swap">
<style>
:root{
  --brand:#c65714;
  --brand-dark:#b54d10;
  --ink:#2b2b2b;
  --muted:#555;
  --grey-bg:#f2f2f2;
  --frame:#efc9a8;
  --white:#fff;
}
*{box-sizing:border-box;margin:0;padding:0}
html,body{width:1200px;height:2489px;overflow:hidden}
body{font-family:"Open Sans",sans-serif;color:var(--ink);background:var(--white);position:relative}
a{color:inherit;text-decoration:none}
ul{list-style:none}

/* header */
.site-header{height:113px;position:relative}
.brand{position:absolute;left:111px;top:30px;display:block}
.brand-name{font-size:20px;font-weight:600;color:var(--brand);border-bottom:1px solid var(--brand);padding-bottom:6px;display:block;width:302px;white-space:nowrap;line-height:26px}
.brand-tag{font-size:10.5px;letter-spacing:2.5px;color:var(--brand);margin-top:6px;white-space:nowrap}
.call{position:absolute;right:111px;top:14px;font-size:17px;color:var(--brand);display:flex;align-items:center;gap:6px}
.call strong{font-size:19px;font-weight:700}
.main-nav{position:absolute;right:111px;top:58px;display:flex;gap:30px;font-size:13px;color:#555}
.main-nav .active{color:var(--brand);font-weight:700}

/* hero */
.hero{height:603px;position:relative;background:linear-gradient(100deg,#c9d3dc 0%,#e8eef2 35%,#b8c0c8 60%,#b9a9c4 100%)}
.hero-panel{position:absolute;left:619px;top:145px;width:470px;height:307px;background:rgba(200,88,20,.95);padding:54px 40px 0 41px;color:var(--white)}
.hero-panel h1{font-size:31px;font-weight:600;margin-bottom:12px;line-height:38px}
.hero-panel p{font-size:16px;line-height:23px;margin-left:2px}
.btn-light{display:inline-block;margin-top:30px;background:var(--white);color:var(--brand);font-size:16px;font-weight:600;padding:12px 32px;border-radius:5px;margin-left:3px}
.dots{position:absolute;left:213px;bottom:30px;display:flex;gap:8px}
.dots span{width:9px;height:9px;border-radius:50%;background:var(--white)}
.dots span:first-child{background:none;border:1px solid var(--white)}

/* about */
.about{height:477px;position:relative}
.about-text{position:absolute;left:112px;top:88px;width:550px}
.about h2{font-size:26px;font-weight:700;color:var(--brand);margin-bottom:12px;line-height:34px}
.about h3{font-size:20px;font-weight:400;color:var(--brand);margin-bottom:18px;margin-left:-2px;line-height:28px}
.about p{font-size:13px;line-height:21.5px;margin-bottom:19px}
.btn{display:inline-block;background:var(--brand);color:var(--white);font-size:16px;font-weight:600;padding:11px 26px;border-radius:5px;margin-top:20px}
.about-photo{position:absolute;left:687px;top:88px;width:402px;height:299px;border:6px solid var(--frame);border-radius:5px;background:linear-gradient(180deg,#9fb6cf 0%,#6d7a86 45%,#4c5e3a 100%)}

/* practice */
.practice{height:468px;background:var(--grey-bg);text-align:center}
.section-title{font-size:26px;font-weight:700;color:var(--brand);padding-top:60px;line-height:34px}
.areas{display:flex;width:1028px;margin:60px auto 0}
.area{width:257px}
.area-icon{width:123px;height:123px;margin:0 auto;border-radius:50%;background:var(--brand);border:3px solid #d98a55;display:flex;align-items:center;justify-content:center}
.area h3{font-size:19px;font-weight:600;line-height:23px;margin:16px 20px 8px}
.area p{font-size:13px;line-height:21px;color:#333;padding:0 25px}

/* blog */
.blog{height:519px;text-align:center}
.blog .section-title{padding-top:62px}
.blog-lead{font-size:16px;margin-top:10px}
.posts{display:flex;gap:26px;width:977px;margin:36px auto 0;text-align:left}
.post{width:308px}
.post-img{height:156px}
.post h3{font-size:19px;font-weight:400;margin:22px 0 6px 4px;white-space:nowrap}
.post p{font-size:13px;line-height:21px;margin-left:4px;padding-right:20px}
.post time{display:block;font-size:11px;color:var(--brand);margin:16px 0 0 7px}

/* footer */
.site-footer{height:309px;background:var(--brand);color:var(--white);position:relative}
.foot-col{position:absolute;top:56px}
.foot-col h4{font-size:13px;font-weight:700;letter-spacing:.5px;margin-bottom:27px}
.foot-col li{font-size:13px;line-height:30px}
.links{left:111px}
.links ul{display:grid;grid-template-columns:206px 100px}
.contact{left:497px;width:400px}
.contact li{display:flex;gap:7px;line-height:17px;margin-bottom:20px;padding-top:7px}
.contact li svg{flex:none;margin-top:3px}
.social{right:111px}
.social li{display:flex;align-items:center;gap:7px}
.social li i{width:11px;height:11px;border-radius:50%;background:var(--white);display:inline-block}
.foot-bottom{position:absolute;left:111px;right:111px;top:252px;border-top:1px solid rgba(255,255,255,.25);padding-top:19px;display:flex;justify-content:space-between;font-size:12px}
.foot-bottom small{font-size:9px;color:#e39a6a}
</style>
</head>
<body>

<header class="site-header">
  <a class="brand" href="#">
    <span class="brand-name">Meridian Crest Legal Group</span>
    <span class="brand-tag">DIVORCE AND PERSONAL INJURY LAWYERS</span>
  </a>
  <div class="call">
    <svg width="16" height="16" viewBox="0 0 24 24"><path fill="#c65714" d="M6.6 10.8a15 15 0 0 0 6.6 6.6l2.2-2.2c.3-.3.7-.4 1-.2 1.1.4 2.3.6 3.6.6.6 0 1 .4 1 1V20c0 .6-.4 1-1 1A17 17 0 0 1 3 4c0-.6.4-1 1-1h3.5c.6 0 1 .4 1 1 0 1.3.2 2.5.6 3.6.1.3 0 .7-.2 1z"/></svg>
    Call Today: <strong>+1.808.555.0148</strong>
  </div>
  <nav class="main-nav">
    <a class="active" href="#">HOME</a><a href="#">ABOUT US</a><a href="#">ATTORNEYS</a><a href="#">PRACTICE AREAS</a><a href="#">BLOG</a><a href="#">CONTACT US</a>
  </nav>
</header>

<section class="hero" role="img" aria-label="Photo of an attorney reviewing documents with a client at a bright office desk">
  <div class="hero-panel">
    <h1>Kona Lawyers of MCLG</h1>
    <p>Over 70 years of combined practice, specializing in Personal Injury, Family &amp; Divorce,Child Custody</p>
    <a class="btn-light" href="#">LEARN MORE</a>
    <div class="dots"><span></span><span></span><span></span></div>
  </div>
</section>

<section class="about">
  <div class="about-text">
    <h2>ABOUT THE KONA LAWYERS OF MCLG</h2>
    <h3>Lawyers Serving the Big Island and Neighboring Islands</h3>
    <p>The experienced attorneys in the Meridian Crest Legal Group's Kailua Kona, Hawaii office provide clients with a wide range of litigation expertise, including legal claims involving divorce &amp; family, personal injury, toxic exposures, intellectual property, and real estate.</p>
    <p>Our Kona office also offers commercial and hospitality litigation expertise on behalf of a wide variety of clients, including restaurants, hotels, property owners, and many others.</p>
    <a class="btn" href="#">LEARN MORE</a>
  </div>
  <div class="about-photo" role="img" aria-label="Photo of a city skyline with high-rise towers above green trees"></div>
</section>

<section class="practice">
  <h2 class="section-title">OUR PRACTICE AREAS</h2>
  <div class="areas">
    <div class="area">
      <div class="area-icon"><svg width="56" height="56" viewBox="0 0 56 56" fill="none" stroke="#fff" stroke-width="2"><circle cx="17" cy="12" r="4"/><path d="M11 34l4-16h4l4 16zM15 34v12M19 34v12"/><circle cx="38" cy="10" r="4"/><path d="M32 18h12v14h-3v14h-6V32h-3z"/><circle cx="28" cy="26" r="3"/><path d="M25 32h6v14h-6z"/></svg></div>
      <h3>Family &amp; Divorce</h3>
      <p>Sunt in culpa qui officia deserunt mollit anim id est laborum sint occaecat cupidatat.</p>
    </div>
    <div class="area">
      <div class="area-icon"><svg width="56" height="56" viewBox="0 0 56 56" fill="none" stroke="#fff" stroke-width="2"><circle cx="28" cy="15" r="8"/><path d="M12 50V38c0-7 6-11 16-11s16 4 16 11v12M20 30l16 16M24 50V40"/></svg></div>
      <h3>Personal Injury</h3>
      <p>Sunt in culpa qui officia deserunt mollit anim id est laborum sint occaecat cupidatat.</p>
    </div>
    <div class="area">
      <div class="area-icon"><svg width="56" height="56" viewBox="0 0 56 56" fill="none" stroke="#fff" stroke-width="2"><path d="M22 40c0-6-8-9-8-18a13 13 0 0 1 26 0c0 9-8 12-8 18z"/><path d="M22 45h10M23 50h8M27 20h16"/><circle cx="46" cy="20" r="3"/></svg></div>
      <h3>Corporate &amp; Intellectual Property</h3>
      <p>Sunt in culpa qui officia deserunt mollit anim id est laborum sint occaecat cupidatat.</p>
    </div>
    <div class="area">
      <div class="area-icon"><svg width="56" height="56" viewBox="0 0 56 56" fill="none" stroke="#fff" stroke-width="2"><path d="M6 26L28 6l22 20M12 21v27h32V21"/><circle cx="22" cy="28" r="3"/><circle cx="34" cy="28" r="3"/><path d="M19 42v-8h6v8M31 42v-8h6v8"/></svg></div>
      <h3>Real Estate</h3>
      <p>Sunt in culpa qui officia deserunt mollit anim id est laborum sint occaecat cupidatat.</p>
    </div>
  </div>
</section>

<section class="blog">
  <h2 class="section-title">LATEST BLOG</h2>
  <p class="blog-lead">At vero eos et accusamus et iusto odio dignissimos ducimus</p>
  <div class="posts">
    <article class="post">
      <div class="post-img" role="img" aria-label="Photo of three professionals meeting in lounge chairs" style="background:linear-gradient(90deg,#6a4a36,#c8c0b0 60%,#8a8478)"></div>
      <h3>Numquam Eius Modi Tempora</h3>
      <p>Class aptent taciti sociosqu ad litora torquent per co nubia nostra per inceptos hymenaeos</p>
      <time>12 JAN 2018</time>
    </article>
    <article class="post">
      <div class="post-img" role="img" aria-label="Photo of business people shaking hands in a conference room" style="background:linear-gradient(180deg,#a9aaa8,#d8d6d2 55%,#6f6a64)"></div>
      <h3>Accusantium Doloremque Lauda</h3>
      <p>Class aptent taciti sociosqu ad litora torquent per co nubia nostra per inceptos hymenaeos</p>
      <time>25 FEB 2018</time>
    </article>
    <article class="post">
      <div class="post-img" role="img" aria-label="Photo of a hand handing a key over a small wooden house model" style="background:linear-gradient(90deg,#3e3a36,#a58a70 55%,#6b5240)"></div>
      <h3>Quia Consequuntur Magni Dolore</h3>
      <p>Class aptent taciti sociosqu ad litora torquent per co nubia nostra per inceptos hymenaeos</p>
      <time>12 MAR 2018</time>
    </article>
  </div>
</section>

<footer class="site-footer">
  <div class="foot-col links">
    <h4>QUICK LINKS</h4>
    <ul><li>Home</li><li>Blog</li><li>About Us</li><li>Gallery</li><li>Practice Areas</li><li>Site Map</li><li>Attorneys</li></ul>
  </div>
  <div class="foot-col contact">
    <h4>CONTACT US</h4>
    <ul>
      <li><svg width="11" height="14" viewBox="0 0 12 16"><path fill="#fff" d="M6 0a6 6 0 0 0-6 6c0 4.5 6 10 6 10s6-5.5 6-10a6 6 0 0 0-6-6zm0 8.5A2.5 2.5 0 1 1 6 3.5a2.5 2.5 0 0 1 0 5z"/></svg><span>Kona Lawyers of Meridian Crest Legal Group,12-3400 Palani Way, Suite 210,Kailua Kona, Hawaii 96740.</span></li>
      <li><svg width="12" height="12" viewBox="0 0 24 24"><path fill="#fff" d="M6.6 10.8a15 15 0 0 0 6.6 6.6l2.2-2.2c.3-.3.7-.4 1-.2 1.1.4 2.3.6 3.6.6.6 0 1 .4 1 1V20c0 .6-.4 1-1 1A17 17 0 0 1 3 4c0-.6.4-1 1-1h3.5c.6 0 1 .4 1 1 0 1.3.2 2.5.6 3.6.1.3 0 .7-.2 1z"/></svg><span>+1.808.555.0148</span></li>
      <li><svg width="13" height="11" viewBox="0 0 16 12"><path fill="#fff" d="M0 0h16v1.5L8 7 0 1.5zM0 3.5l8 5.5 8-5.5V12H0z"/></svg><span>clients@tarnadvocate.example</span></li>
    </ul>
  </div>
  <div class="foot-col social">
    <h4>CONNECT WITH US</h4>
    <ul><li><i></i>Circlehub</li><li><i></i>Chatterlane</li><li><i></i>Snapframe</li><li><i></i>Clipstream</li></ul>
  </div>
  <div class="foot-bottom">
    <span>Copyrights © 2019 Meridian Crest Legal Group. All rights reserved.</span>
    <small>Terms and Conditions | Privacy Policy</small>
  </div>
</footer>

</body>
</html>
```